Mexican Restaurant needs a new Menu Design

Mexican restaurant LA MARIPOSA AZUL is renewing its menu, so we need something new.
Since our inception we have given the task of rescuing ingredients, recipes, and traditional and representatives dishes of the culinary techniques of yesteryear.
We are the only restaurant in Guadalajara that manufactures its own dairy natural as fresh cheese, the cream and our already well-known and traditional jocoqui. In addition, we produce organic ranch egg and are currently in the development of organic vegetables cultivated on the slopes of the old Hill which gives our plants benefit from an exceptional microclimate.
Find more information about the restaurant in www.lamariposaazul.com.
The menu needs to have the full list of products with the prices, some phrases that speak of the philosophy of the ranch-style-living, photos.
We need the cover, back cover and interiors.
Updates
Thank you so much for the proposals you have submitted for the menu design. We are looking them carefully.
Thank you very much for taking your time to design a proposal for our menu!!!
Target Market(s)
The target is very wide (28-40 yrs.): Young executives, Young families, Housewives.
Industry/Entity Type
Restaurant
Look and feel
Each slider illustrates characteristics of the customer's brand and the style your logo design should communicate.

```html
<!DOCTYPE html>
<html lang="es">
<head>
<meta charset="utf-8">
<title>La Mariposa Azul – Menú, páginas 9 y 10</title>
<link href="https://fonts.googleapis.com/css2?family=Marmelad&family=Vollkorn:wght@700&display=swap" rel="stylesheet">
<style>
  :root {
    --canvas: #eeeeee;
    --frame-red: #e3221c;
    --brush-red: #dd1f1f;
    --parchment-light: #f6e9c4;
    --parchment-mid: #efdcaa;
    --parchment-dark: #e2c78c;
    --ink: #2b2118;
    --ink-soft: #3d3024;
    --rule: #5a4a3a;
    --page-num: #5a4a3a;
    --white: #ffffff;
    --strip-dark: #3a0d08;
    --strip-mid: #6d1a10;
  }
  * { margin: 0; padding: 0; box-sizing: border-box; }
  html, body { width: 1200px; height: 901px; overflow: hidden; }
  body { background: var(--canvas); position: relative; }

  .page {
    position: absolute;
    top: 30px;
    width: 570px;
    height: 828px;
    border: 4px solid var(--frame-red);
    border-bottom: none;
    background:
      radial-gradient(ellipse at 30% 25%, var(--parchment-light) 0%, transparent 60%),
      radial-gradient(ellipse at 75% 70%, var(--parchment-light) 0%, transparent 55%),
      linear-gradient(160deg, var(--parchment-mid) 0%, var(--parchment-light) 45%, var(--parchment-dark) 100%);
    overflow: hidden;
  }
  .page--left { left: 22px; }
  .page--right { left: 609px; }

  .page-number {
    position: absolute;
    top: 3px;
    right: 10px;
    font-family: "Marmelad", sans-serif;
    font-size: 17px;
    color: var(--page-num);
  }

  .item {
    position: absolute;
    left: 14px;
    right: 16px;
  }
  .item-head {
    display: flex;
    justify-content: space-between;
    align-items: baseline;
    border-bottom: 1px solid var(--rule);
    padding-bottom: 2px;
    padding-right: 4px;
    font-family: "Marmelad", sans-serif;
    font-size: 18px;
    line-height: 24px;
    color: var(--ink);
  }
  .item-price { font-size: 17px; letter-spacing: 0.5px; }
  .item-desc {
    margin-top: 5px;
    font-family: "Marmelad", sans-serif;
    font-size: 13px;
    line-height: 17px;
    color: var(--ink-soft);
  }

  .section-title {
    position: absolute;
    height: 36px;
    display: flex;
    align-items: center;
  }
  .section-title svg { position: absolute; inset: 0; width: 100%; height: 100%; }
  .section-title span {
    position: relative;
    padding-left: 16px;
    font-family: "Vollkorn", serif;
    font-weight: 700;
    font-size: 25px;
    color: var(--white);
    letter-spacing: 0.3px;
  }

  .photo-strip {
    position: absolute;
    top: 755px;
    width: 570px;
    height: 102px;
    background:
      radial-gradient(circle at 12% 50%, #b89560 0 52px, transparent 53px),
      radial-gradient(circle at 37% 50%, #b87c4a 0 52px, transparent 53px),
      radial-gradient(circle at 62% 50%, #a86c3c 0 52px, transparent 53px),
      radial-gradient(circle at 88% 50%, #a05a3c 0 52px, transparent 53px),
      linear-gradient(90deg, var(--strip-dark), var(--strip-mid), var(--strip-dark));
  }
  .photo-strip--left { left: 22px; }
  .photo-strip--right { left: 609px; }
</style>
</head>
<body>

<section class="page page--left">
  <div class="page-number">page 9</div>

  <article class="item" style="top:39px">
    <div class="item-head"><span class="item-name">Enchiladas en Mole Artesanal</span><span class="item-price">00.00</span></div>
    <p class="item-desc">Rellenas de Pollito y Bañadas en Nuestro Mole, El Meritito de la Receta Original de 36 ingredientes.</p>
  </article>

  <article class="item" style="top:109px; left:13px">
    <div class="item-head"><span class="item-name">Enchiladas "Doña Lupe"</span><span class="item-price">00.00</span></div>
    <p class="item-desc">Adobadas con Lechuguita y rellenas de Pollito o Queso Fresco Artesanal. Su saborcito recuerda a las Fondas del Mercado.</p>
  </article>

  <article class="item" style="top:182px">
    <div class="item-head"><span class="item-name">Enchiladas Poblanas</span><span class="item-price">00.00</span></div>
    <p class="item-desc">Bañadas en Una Salsa de Chile Poblano. Pueden ser Rellenas de Pollito o Queso Fresco del que Elaboramos Nosotros Mismos en Nuestra Quesería Artesanal.</p>
  </article>

  <article class="item" style="top:252px">
    <div class="item-head"><span class="item-name">Enchiladas Tex-Mex</span><span class="item-price">00.00</span></div>
    <p class="item-desc">Bañadas en una Salsita Colorada y Rellenas de Fajitas de Arrachera Importada ¡ Deli-ciosous, dirían en el otro Lado!</p>
  </article>

  <article class="item" style="top:323px">
    <div class="item-head"><span class="item-name">Enchiladas Verdis</span><span class="item-price">00.00</span></div>
    <p class="item-desc">En salsa de tomatito verdi.</p>
  </article>

  <h2 class="section-title" style="top:384px; left:6px; width:242px">
    <svg viewBox="0 0 242 36" preserveAspectRatio="none" aria-hidden="true">
      <path d="M6 6 L230 3 L240 12 L236 26 L226 34 L14 33 L2 26 L4 14 Z" fill="var(--brush-red)"/>
    </svg>
    <span>Nuestra parrilla</span>
  </h2>

  <article class="item" style="top:425px">
    <div class="item-head"><span class="item-name">Medallones de Caña de Filete Jugoso de Res</span><span class="item-price">00.00</span></div>
    <p class="item-desc">Jugositos Medallones de Caña de Filete de Res pasados por nuestro Grill de Leña Natural acompañados de Chilaquiles Coloraos, Nopalitos a la Mexicana y Frijolitos Fritos.</p>
  </article>

  <article class="item" style="top:512px">
    <div class="item-head"><span class="item-name">Filete de Res "Al Arriero"</span><span class="item-price">00.00</span></div>
    <p class="item-desc">Medallones de Filete al Grill de Leña Bañados en Salsa de Mantequilla al Limón con Papita y Cebollita Cambray, Chilitos de Árbol y Champiñones.</p>
  </article>

  <article class="item" style="top:587px">
    <div class="item-head"><span class="item-name">Arrachera Seleccionada 300 Grs.</span><span class="item-price">00.00</span></div>
    <p class="item-desc">IMportada de los Junaites´n ¡Bien Buena!</p>
  </article>

  <article class="item" style="top:640px; left:17px">
    <div class="item-head"><span class="item-name">Pollo a la Talla</span><span class="item-price">00.00</span></div>
    <p class="item-desc">Asadito en nuestro Grill de Leña Natural y Adobadito Con la mera Receta Original de la Costa.</p>
  </article>
</section>

<div class="photo-strip photo-strip--left" role="img" aria-label="Fotografías de cuatro platos: enchiladas verdes, enchiladas en mole, pollo a la talla y arrachera, sobre fondo de chiles secos"></div>

<section class="page page--right">
  <div class="page-number">page 10</div>

  <article class="item" style="top:39px">
    <div class="item-head"><span class="item-name">Rib Ai 300 Grs.</span><span class="item-price">00.00</span></div>
    <p class="item-desc">O Rib Eye si prefiere. Calidad Choice desde el Meritito Canadá. Va acompañado de Chilaquiles Coloraos, Nopalitos a la Mexicana y Frijoltos Fritos.</p>
  </article>

  <h2 class="section-title" style="top:109px; left:14px; width:196px">
    <svg viewBox="0 0 196 36" preserveAspectRatio="none" aria-hidden="true">
      <path d="M5 5 L186 3 L194 12 L191 27 L182 34 L12 33 L2 25 L3 13 Z" fill="var(--brush-red)"/>
    </svg>
    <span style="padding-left:12px">Platos Juertes</span>
  </h2>

  <article class="item" style="top:155px">
    <div class="item-head"><span class="item-name">Aguachile de Camarón</span><span class="item-price">00.00</span></div>
    <p class="item-desc">Camarones Frescos en Salsa de Chile Serrano, ideales como Botanita para Compartir con Tostaditas Raspadas en Metate o Como Plato Prencipal.</p>
  </article>

  <article class="item" style="top:230px">
    <div class="item-head"><span class="item-name">Filete de Pescado "Al Arriero"</span><span class="item-price">00.00</span></div>
    <p class="item-desc">Filetito de Pescado Blanco de Oriente En salsa de Mantequilla al Limón con Papita Cambray y Cebollita también Cambray, con Chilitos de Árbol y Champiñones.</p>
  </article>

  <article class="item" style="top:303px">
    <div class="item-head"><span class="item-name">Camarones al Mojo de Ajo</span><span class="item-price">00.00</span></div>
    <p class="item-desc">Pueden ser en Nuestro Ajillo Tradicional o en Ajillo de Jamaica.</p>
  </article>

  <article class="item" style="top:357px">
    <div class="item-head"><span class="item-name">Camarones "A la Diabla"</span><span class="item-price">00.00</span></div>
    <p class="item-desc">Usté puede solicitar "Que tan enojada quiere que salga la Diabla" oséase, que tan picantes los quiere.</p>
  </article>

  <article class="item" style="top:430px">
    <div class="item-head"><span class="item-name">Chamorro Horneao</span><span class="item-price">00.00</span></div>
    <p class="item-desc">Chamorro de Cerdito Adobado, Horneao en su Jugo y con Frijoilitos de la Olla.</p>
  </article>

  <article class="item" style="top:484px">
    <div class="item-head"><span class="item-name">Filete de Pescado en Mole Poblano</span><span class="item-price">00.00</span></div>
    <p class="item-desc">Una Variante Muy Interesante para Nuestro Mole, el que tiene la receta original de 36 ingredientes.</p>
  </article>

  <article class="item" style="top:556px">
    <div class="item-head"><span class="item-name">Pollo "La Mariposa Azul"</span><span class="item-price">00.00</span></div>
    <p class="item-desc">En salsa de Betabel al Chipotle, por algo será que le pusimos el Nombre de la Casa. El color de la Salsa es Naturalito "Aunque Usté No lo Crea" .</p>
  </article>

  <article class="item" style="top:625px">
    <div class="item-head"><span class="item-name">Pollo en Mole Poblano Artesanal</span><span class="item-price">00.00</span></div>
    <p class="item-desc">Nuestro Mole tiene la Receta Original de 36 ingredientes ¿Cuántos alcanza Usté a Identificar?</p>
  </article>
</section>

<div class="photo-strip photo-strip--right" role="img" aria-label="Fotografías de cuatro platos: rib eye, aguachile de camarón, camarones a la diabla y pollo en mole, sobre fondo de chiles secos"></div>

</body>
</html>
```